TK Stationery - Modern Contemporary

Develop modern template for Letterhead and Stationery (business card, letterhead, envelopes) using the TK Logo and Icon

Colors
0054AA
0677BA
7BADD7
CADEEF
E8F1F8
00AB8E
00BBA5
67D7C9
C6EFE9
E9F9F6
EE7325
F08F49
F5BC92
FAE3D3
FDF4ED
6B429C
8869AF
B7A5CE
E3DAEB
F3F0F8

```html
<!DOCTYPE html>
<html lang="en">
<head>
<meta charset="utf-8">
<title>TK Verdant Letterhead</title>
<link rel="stylesheet" href="https://fonts.googleapis.com/css2?family=Arimo:wght@400;700&family=Questrial&display=swap">
<style>
  :root {
    --backdrop: #cdcccd;
    --paper: #ffffff;
    --brand-green: #3aae72;
    --brand-navy: #272c48;
    --accent-orange: #ee7325;
    --text-grey: #545454;
    --signature-ink: #4a4a4a;
  }
  * { box-sizing: border-box; margin: 0; padding: 0; }
  html, body { width: 1173px; height: 1200px; overflow: hidden; }
  body { background: var(--backdrop); position: relative; font-family: "Arimo", Arial, sans-serif; }

  .letterhead {
    position: absolute; left: 230px; top: 96px; width: 713px; height: 1009px;
    background: var(--paper);
    box-shadow: 2px 2px 4px rgba(0,0,0,.35);
  }

  .header-band { position: absolute; top: 60px; height: 9px; background: var(--brand-green); }
  .header-band--left { left: 0; width: 237px; }
  .header-band--right { left: 475px; right: 0; }
  .header-rule { position: absolute; top: 76px; height: 2px; background: var(--brand-navy); }
  .header-rule--left { left: 0; width: 387px; }
  .header-rule--right { left: 398px; right: 0; }

  .brand-name {
    position: absolute; left: 243px; top: 40px; width: 228px;
    display: flex; align-items: center; justify-content: center; gap: 6px;
    font-family: "Arimo", Arial, sans-serif; font-size: 31px; line-height: 36px;
    color: var(--brand-navy); letter-spacing: 0.5px;
  }
  .brand-dot { width: 6px; height: 6px; border-radius: 50%; background: var(--accent-orange); }

  .greeting {
    position: absolute; left: 65px; top: 309px;
    font-family: "Questrial", "Century Gothic", sans-serif; font-weight: 700;
    font-size: 16.5px; color: var(--text-grey);
  }

  .letter-body { position: absolute; left: 63px; top: 356px; width: 586px; color: var(--text-grey); }
  .letter-body p { font-size: 11.4px; line-height: 14.8px; margin-bottom: 12.4px; }

  .sign-off {
    position: absolute; left: 65px; top: 660px;
    font-family: "Questrial", "Century Gothic", sans-serif; font-weight: 700;
    font-size: 9px; color: var(--text-grey);
  }
  .signature {
    position: absolute; left: 64px; top: 701px; width: 117px; height: 35px;
    border-radius: 4px;
    background: linear-gradient(90deg, rgba(74,74,74,.18), rgba(74,74,74,.08));
  }

  .footer { position: absolute; left: 164px; top: 949px; width: 384px; text-align: center; color: var(--brand-navy); }
  .footer-address { font-size: 12px; line-height: 15px; padding-bottom: 2px; border-bottom: 1px solid var(--brand-navy); }
  .footer-contacts {
    display: flex; justify-content: center; align-items: center; gap: 10px;
    margin-top: 4px; font-size: 12px; line-height: 16px; white-space: nowrap;
  }
  .contact-item { display: flex; align-items: center; gap: 7px; }
  .contact-icon { width: 9px; height: 9px; fill: var(--brand-green); }
</style>
</head>
<body>
  <main class="letterhead">
    <div class="header-band header-band--left"></div>
    <div class="header-band header-band--right"></div>
    <div class="header-rule header-rule--left"></div>
    <div class="header-rule header-rule--right"></div>

    <div class="brand-name"><span>tk verdant</span><span class="brand-dot"></span></div>

    <h1 class="greeting">Dear Mr. Smith,</h1>

    <section class="letter-body">
      <p>Lorem ipsum dolor sit amet, consectetuer adipiscing elit, sed diam nonmmy nibh euismod tincidunt ut laor eet dolore magna aliquam erat volutpat. Ut wisi enim ad minim veniam, quis nostrud exerci tationmcorper suscipit lobortis nisl ut aliquip ex ea commodo consequat. Duis autem vel eum iriure dolor in hendrerit in vulputate velit esse molestie consequat, vel illum dolore eu feugiat</p>
      <p>Rorem ipsum dolor sit amet, consectetuer adipiscing elit, sed diam nonmmy nibh euismod tincidunt ut laor eet dolore magna aliquam erat volutpat. Ut wisi enim ad minim veniam, quis nostrud exerci tationmcorper suscipit lobortis nisl ut aliquip ex ea commodo consequat. Duis autem vel eum iriure dolor in hendrerit in vulputate velit esse molest</p>
      <p>Dorem ipsum dolor sit amet, consectetuer adipiscing elit, sed diam nonmmy nibh euismod tincidunt ut laor eet dolore magna aliquam erat volutpat. Ut wisi enim ad minim veniam, quis nostrud exerci tationmcorper suscipit lobortis nisl ut aliquip ex ea commodo consequat. Duis autem vel eum iriure dolor in hendrerit in suscipit lobortis nisl ut aliquip ex ea commodo consequat. Duis autem vel eum iriure dolor in hendrerit in vulputate velit esse molestie consequat, vel illum</p>
      <p>Sorem ipsum dolor sit amet, consectetuer adipiscing elit, sed diam nonmmy nibh euismod tincidunt ut laor eet dolore magna aliquam erat volutpat. Ut wisi enim ad minim veniam, quis nostrud exerci tationmcorper suscipit lobortis nisl ut aliquip ex ea commodo consequat. Duis autem vel eum iriure dolor in</p>
    </section>

    <p class="sign-off">Sincerely,</p>
    <div class="signature" role="img" aria-label="Handwritten signature of the sender"></div>

    <footer class="footer">
      <p class="footer-address">Your address, city, state, ZIP 0000</p>
      <div class="footer-contacts">
        <span class="contact-item">
          <svg class="contact-icon" viewBox="0 0 10 10" aria-hidden="true"><path d="M2 0.5 L3.6 2.6 L2.8 3.6 Q3.8 5.8 6.3 7.2 L7.3 6.4 L9.5 8 L8.3 9.5 Q4.5 9.2 1.6 5.8 Q0.3 3.6 0.6 1.6 Z"/></svg>
          123-456-2100
        </span>
        <span class="contact-item">
          <svg class="contact-icon" viewBox="0 0 10 10" aria-hidden="true"><path d="M0.5 2 H9.5 V8 H0.5 Z M1 2.4 L5 5.4 L9 2.4" stroke="#fff" stroke-width="0.7"/></svg>
          info@tkverdant.com
        </span>
        <span class="contact-item">
          <svg class="contact-icon" viewBox="0 0 10 10" aria-hidden="true"><circle cx="5" cy="5" r="4.6"/><path d="M0.6 5 H9.4 M5 0.4 Q2.6 5 5 9.6 M5 0.4 Q7.4 5 5 9.6" stroke="#fff" stroke-width="0.6" fill="none"/></svg>
          www.tkverdant.com
        </span>
      </div>
    </footer>
  </main>
</body>
</html>
```